Flyer Design Project for lawn care business

I need a flyer designed for my lawn care business, "Fenwick's Upkeep Services".  It is a family owned small landscaping company. I was thinking something that I can print  2- 3 per page.
I have  2 different logos I can upload to give an idea.  I have seen some I like that are colorfull with neat graphics but I also like some that are simple and elegant.  I would like something that catches your eye and looks professionaly done.

Target Market(s)
Homeowners in Durham, North Carolina with homes usually valued $200,000 or more.
Industry/Entity Type
Landscaping
Requirements
Must have
- I would like the address of my website listed on it, www.fenwickupkeepservices-example.com
I would like for it to say somewhere, 50% off first service with seasonal service.
Not sure if I want to list some of the services that I offer or just say full service lawn care.
Nice to have
- I have a logo with a bull pushing a lawn mower.  I live in Durham, NC also known as the Bull City.  I am not in love with the logo so feel free to change it or not use it at all.

```html
<!DOCTYPE html>
<html lang="en">
<head>
<meta charset="utf-8">
<title>Fenwick's Upkeep Services – Flyer</title>
<link href="https://fonts.googleapis.com/css2?family=Fredoka:wght@600&family=Gabriela&family=Oswald:wght@500&display=swap" rel="stylesheet">
<style>
  :root {
    --ink: #000000;
    --sky: #a3dbeb;
    --orange: #f26a10;
    --red: #ee1c25;
    --white: #ffffff;
    --grass: #3f9a2c;
    --grey-light: #e6e6e6;
    --grey-mid: #8a8a8a;
    --grey-dark: #2a2a2a;
  }
  * { margin: 0; padding: 0; box-sizing: border-box; }
  html, body {
    width: 1200px; height: 900px; overflow: hidden; background: var(--white);
  }
  .flyer {
    position: absolute; left: 18px; top: 22px; width: 1166px; height: 856px;
    overflow: hidden;
    background: linear-gradient(180deg, #dcdcdc 0%, #b5b5b5 35%, #6d6d6d 65%, #0c0c0c 100%);
  }
  .backdrop { position: absolute; inset: 0; }
  .mower-art {
    position: absolute; left: 640px; top: 230px; width: 526px; height: 560px;
    background: radial-gradient(ellipse at 60% 55%, rgba(70,70,70,0.55) 0%, rgba(70,70,70,0.25) 45%, rgba(70,70,70,0) 75%);
  }
  .brand {
    position: absolute; left: 196px; top: 120px;
    display: flex; align-items: center; gap: 22px;
  }
  .brand-dot {
    width: 120px; height: 120px; border-radius: 50%; background: var(--grass);
  }
  .brand-name {
    font-family: "Fredoka", sans-serif; font-weight: 600;
    font-size: 104px; line-height: 1; color: var(--orange);
    letter-spacing: 1px;
  }
  .tagline {
    position: absolute; left: 160px; top: 258px; width: 800px; text-align: center;
    font-family: "Fredoka", sans-serif; font-weight: 600;
    font-size: 60px; line-height: 1; color: var(--red);
  }
  .offer {
    position: absolute; left: 52px; top: 408px;
    font-family: "Gabriela", serif; font-size: 39px; color: var(--ink);
    text-shadow: 2px 3px 3px rgba(0,0,0,0.3);
  }
  .service-line {
    position: absolute; left: 22px; top: 728px;
    font-family: "Gabriela", serif; font-size: 47px; color: var(--white);
  }
  .web-address {
    position: absolute; left: 22px; top: 786px;
    font-family: "Oswald", sans-serif; font-weight: 500;
    font-size: 44px; line-height: 1; color: var(--red);
    transform: scaleX(0.86); transform-origin: left top;
  }
  .corner-mark {
    position: absolute; left: 846px; top: 730px; width: 300px; height: 110px;
    display: flex; align-items: center; justify-content: center; gap: 14px;
    border-bottom: 2px solid #b8860b;
  }
  .corner-square { width: 48px; height: 48px; background: var(--grass); }
  .corner-name {
    font-family: "Fredoka", sans-serif; font-weight: 600; font-size: 38px; color: var(--grass);
  }
</style>
</head>
<body>
<main class="flyer">
  <svg class="backdrop" width="1166" height="856" viewBox="0 0 1166 856" aria-hidden="true">
    <path d="M560 0 C 760 40, 1000 160, 1166 330 L 1166 0 Z" fill="#f4f4f4"/>
    <path d="M420 0 C 600 60, 780 230, 760 856 L 900 856 C 930 400, 800 120, 600 0 Z" fill="rgba(255,255,255,0.12)"/>
  </svg>

  <div class="mower-art" role="img" aria-label="Faint illustration of a push lawn mower"></div>

  <svg class="backdrop" width="1166" height="856" viewBox="0 0 1166 856" aria-hidden="true">
    <path class="speech-shadow" transform="translate(8,10)"
      d="M6 300 C 40 250, 160 218, 420 222 C 700 226, 900 250, 1010 244
         C 990 300, 930 380, 880 440 C 820 520, 700 600, 520 620
         C 400 632, 300 636, 220 640 C 210 660, 200 680, 192 690
         C 170 670, 150 650, 120 630 C 50 600, 0 520, 0 420 Z" fill="var(--ink)"/>
    <path class="speech-bubble"
      d="M6 300 C 40 250, 160 218, 420 222 C 700 226, 900 250, 1010 244
         C 990 300, 930 380, 880 440 C 820 520, 700 600, 520 620
         C 400 632, 300 636, 220 640 C 210 660, 200 680, 192 690
         C 170 670, 150 650, 120 630 C 50 600, 0 520, 0 420 Z" fill="var(--sky)"/>
  </svg>

  <div class="brand">
    <span class="brand-dot"></span>
    <h1 class="brand-name">FENWICK'S</h1>
  </div>
  <h2 class="tagline">UPKEEP SERVICES</h2>

  <p class="offer">50% off first service with seasonal service.</p>

  <p class="service-line">Full Service Lawn Care.</p>
  <p class="web-address">www.fenwickupkeepservices-example.com</p>

  <div class="corner-mark">
    <span class="corner-square"></span>
    <span class="corner-name">Fenwick's</span>
  </div>
</main>
</body>
</html>
```